Summit Ridge Business Card

Side 1: Summit Ridge Logo (logo without Maltese cross) with industrial rope rescue related theme. Our company services - TRAINING - Fire Training, Confined Space Rescue Training, Rope Rescue training, Hazmat Training, Incident Command, EMS, Pump Operations Training. Website - summitridgeexample.com.
Side 2: Summit Ridge Fire Department Logo (logo with Maltese cross) with Firefighter related theme. Company (division) services - FIELD SERVICES - Fire Department, Stand-by Rescue, Safety, EMS, Planning. "Supporting the Emergency Response Community Since 1967"

Add contact information wherever it makes since (Name, Email, Phone).
I would like it to represent the Summit Ridge Fire Department Logo as a division not as a separate entity without saying it, possibly by depicting it in the background of Side 2 instead of being a standalone picture like the logo on Side 1.

```html
<!DOCTYPE html>
<html lang="en">
<head>
<meta charset="UTF-8">
<title>Summit Ridge Business Card</title>
<link href="https://fonts.googleapis.com/css2?family=Montserrat:wght@400;600;700;800&display=swap" rel="stylesheet">
<style>
  :root {
    --page: #1b1b1d;
    --card: #262628;
    --red: #e41e26;
    --white: #ffffff;
    --muted: #d4d4d6;
    --soft: #8c8c90;
    --emboss: #3a3a3d;
    --emboss-light: #46464a;
  }
  * { margin: 0; padding: 0; box-sizing: border-box; }
  html, body { width: 1200px; height: 900px; overflow: hidden; background: var(--page); }
  body { font-family: "Montserrat", sans-serif; position: relative; }

  .card {
    position: absolute;
    left: 250px;
    width: 700px;
    height: 400px;
    background: var(--card);
    border-radius: 22px;
    overflow: hidden;
    border-bottom: 4px solid var(--red);
    box-shadow: 0 18px 40px rgba(0,0,0,.55);
  }
  .card--back { top: 35px; }
  .card--front { top: 465px; }

  .theme-backdrop { position: absolute; inset: 0; }
  .theme-backdrop--rope {
    background: radial-gradient(ellipse at 50% 35%, #2e2e31 0%, var(--card) 70%);
  }
  .theme-backdrop--fire {
    background: radial-gradient(ellipse at 85% 20%, #32282a 0%, var(--card) 60%);
  }

  /* side 1: training */
  .training {
    position: absolute; inset: 0;
    display: flex; flex-direction: column; align-items: center;
    padding-top: 92px;
  }
  .training__mark { display: flex; align-items: center; gap: 18px; }
  .training__dot { width: 34px; height: 34px; border-radius: 50%; background: var(--emboss); }
  .training__name {
    font-weight: 800; font-size: 46px; letter-spacing: 4px; line-height: 1;
    color: var(--emboss); text-transform: uppercase;
  }
  .training__rule { width: 420px; height: 2px; background: var(--emboss); margin: 22px 0 20px; }
  .training__heading {
    font-weight: 700; font-size: 13px; letter-spacing: 4px;
    color: var(--red); text-transform: uppercase;
  }
  .training__list {
    list-style: none; width: 560px; margin-top: 12px;
    display: flex; flex-wrap: wrap; justify-content: center; gap: 6px 18px;
    color: var(--soft); font-size: 13px;
  }
  .training__web { position: absolute; bottom: 26px; color: var(--soft); font-size: 13px; letter-spacing: 1px; }

  /* side 2: field services */
  .front-shapes { position: absolute; inset: 0; }
  .brand {
    position: absolute; top: 34px; right: 48px;
    display: flex; align-items: center; gap: 10px;
  }
  .brand__square { width: 18px; height: 18px; background: var(--red); }
  .brand__name {
    font-weight: 800; font-size: 24px; letter-spacing: 2px; line-height: 1;
    color: var(--red); text-transform: uppercase;
  }
  .tagline {
    position: absolute; top: 72px; right: 48px;
    color: var(--soft); font-size: 11px; letter-spacing: .3px;
  }
  .division {
    position: absolute; top: 108px; left: 36px;
    display: flex; align-items: center; gap: 16px;
  }
  .division__dot { width: 56px; height: 56px; border-radius: 50%; background: var(--emboss); }
  .division__name {
    font-weight: 800; font-size: 28px; line-height: 1.1; letter-spacing: 2px;
    color: var(--emboss); text-transform: uppercase;
  }
  .field {
    position: absolute; top: 112px; right: 48px; width: 170px; text-align: right;
  }
  .field__heading {
    font-weight: 700; font-size: 12px; letter-spacing: 3px;
    color: var(--red); text-transform: uppercase;
  }
  .field__list { list-style: none; margin-top: 6px; color: var(--muted); font-size: 12px; line-height: 17px; }
  .address {
    position: absolute; top: 268px; right: 48px; text-align: right;
    color: var(--muted); font-size: 13px; line-height: 1.35; font-style: normal;
  }
  .website-band {
    position: absolute; right: 40px; bottom: 12px;
    color: var(--white); font-size: 14px;
  }
  .person { position: absolute; left: 36px; top: 238px; color: var(--white); }
  .person__name { font-weight: 700; font-size: 28px; line-height: 1; }
  .person__title { font-size: 14px; margin-top: 4px; }
  .contacts {
    position: absolute; left: 80px; top: 306px;
    list-style: none; color: var(--muted); font-size: 15px;
  }
  .contacts li { display: flex; align-items: center; gap: 12px; height: 24px; }
  .contacts svg { width: 14px; height: 14px; fill: var(--red); flex: none; }
</style>
</head>
<body>

<section class="card card--back" aria-label="Card side one, training">
  <div class="theme-backdrop theme-backdrop--rope" role="img" aria-label="Industrial rope rescue backdrop"></div>
  <div class="training">
    <div class="training__mark">
      <span class="training__dot"></span>
      <span class="training__name">Summit Ridge</span>
    </div>
    <div class="training__rule"></div>
    <p class="training__heading">Training</p>
    <ul class="training__list">
      <li>Fire Training</li>
      <li>Confined Space Rescue Training</li>
      <li>Rope Rescue Training</li>
      <li>Hazmat Training</li>
      <li>Incident Command</li>
      <li>EMS</li>
      <li>Pump Operations Training</li>
    </ul>
    <p class="training__web">www.summitridgeexample.com</p>
  </div>
</section>

<section class="card card--front" aria-label="Card side two, field services">
  <div class="theme-backdrop theme-backdrop--fire" role="img" aria-label="Firefighter backdrop"></div>

  <div class="division" aria-label="Summit Ridge Fire Department">
    <span class="division__dot"></span>
    <span class="division__name">Summit Ridge<br>Fire Department</span>
  </div>

  <svg class="front-shapes" viewBox="0 0 700 400" aria-hidden="true">
    <polygon points="0,232 300,232 250,290 0,290" fill="var(--red)"/>
    <polygon points="420,400 420,368 440,352 700,352 700,400" fill="var(--red)"/>
  </svg>

  <div class="brand">
    <span class="brand__square"></span>
    <span class="brand__name">Summit Ridge</span>
  </div>
  <p class="tagline">Supporting the Emergency Response Community Since 1967</p>

  <div class="field">
    <p class="field__heading">Field Services</p>
    <ul class="field__list">
      <li>Fire Department</li>
      <li>Stand-by Rescue</li>
      <li>Safety</li>
      <li>EMS</li>
      <li>Planning</li>
    </ul>
  </div>

  <address class="address">218 Quarry Road<br>Halton ON<br>L7A 2K4</address>

  <div class="person">
    <p class="person__name">Daniel Moreau</p>
    <p class="person__title">Managing Director</p>
  </div>

  <ul class="contacts">
    <li>
      <svg viewBox="0 0 16 16"><path d="M3 1l3 3-1.5 2a9 9 0 0 0 5.5 5.5L12 10l3 3-2 2C6 15 1 10 1 3z"/></svg>
      877-555-0142
    </li>
    <li>
      <svg viewBox="0 0 16 16"><path d="M1 3h14v10H1z"/></svg>
      info@summitridgeexample.com
    </li>
    <li>
      <svg viewBox="0 0 16 16"><circle cx="8" cy="8" r="7"/></svg>
      www.summitridgeexample.com
    </li>
  </ul>

  <p class="website-band">www.summitridgeexample.com</p>
</section>

</body>
</html>
```